SaaS / Consulting / Solution website redesign

We need a website design that:
- Is completely different than our current design : https://plumvessel.net
- Has a very minimal amount of copy
- Changes our positioning from a SaaS application to a solutions company. Solutions company means that we help our customers solve their problems with consulting, training, and tools. An example of a solutions company is here: https://oldpages.example/web/20130111103320/http://www.brindlework.com:80/
- Does not make us look like a start up
- Is more people oriented than technology oriented

We need a designer that:
- Is a rebel at heart
- Is a minimalist
- Tells us why our current site sucks
- Can disagree with us
- Can also do copywriting or already has a copywriter that can help
- Is ok with saying we have capability that we don't in order to see if people actually want that
- Can understand the difference between our grand vision and where we need to focus ourselves today in order to get there

Who we are:
- Entrepreneurs
- Programmers
- Consultants
- Investors

Here's our design goals:
#1 Get customers, investors, employers, and partners excited about our unique and clearly articulated value proposition
#2 Get people to contact us asking for help with their programs
#3 Position ourselves as an expert in the skills based volunteering, mentorship, and group collaboration
#4 Make it easy for people, who already know who we are, to register online

What our grand vision is:
- Create a marketplace where any person can go to our site and find time with anyone they need to meet with. Whether that is their hair stylist, school advisor, parent of your kids class, dentist, attorney, etc.

What will you get if you win:
- In addition to the prize of this project we will have many landing pages and other revisions we will need in the future. We currently don't have a designer or copywriter and need to add that capability to our team

Who do we need to appeal to:
- Directors that are launching innovative programs inside organizations
- IT personnel who are trying to disqualify our technology so they don't have to support it or deal with it when it doesn't go well
- Enterprise IT architects who don't want our product being on its own island within their organization totally incompatible with everything else. Architects which are trying to assess how our platform will co-exist with all their other platforms
- Vice Presidents who want to help their directors understand that we don't have enough experience to help them
- Program managers who have to juggle a million things and need a tool that actually helps instead of confuses them and adds more work for them.
- Program managers & directors that have been given ambiguous goals by their board of directors like "improve retention, increase engagement, create innovation, get people to collaborate." And who have no idea where to start or how to deliver on things like that.
- Program managers, directors, and vice presidents that are trying to understand how our technology and services fit into their existing technology and capability
- Employees who are bored and uninspired with their current tools and are hoping for some excitement in their life. Kind of like candy or a double espresso.
- Investors who think, our company like all the rest, are going to waste their money and make them look like a fool

Other information:
-The CSS and html needs to be responsive

-Our registration onboarding flow needs to collect this information:
User first name
user last name
user email
(verify their email)
user phone number
(verify their phone number)
User profile image (optional)
User profile summary (optional, like a bio, freeform text fiels)
If applicable: Register their organization
Organization name
Organization image (optional)
Account Mailing address
account Billing address (could be same as mailing address)
account Billing email address (could be same as user address)
account Product selection (pricing tier)
account Credit card information

The designs I am getting are a good start but they are only the front page. I just want you to know that I am expecting and need more than a landing page to complete the design. I will likely need a page that outlines the benefits and features of the product itself, how its different than our competitors, which will not be on the front page. I will need a registration flow. I will need a blog page design so we can post blog articles, I will need a team page, a page that goes into detail on our training, our services. I will likely need a page that shows all news and media we have been in. I need to show customer and user quotes, case studies, a way to contact us, partners, general resources like on collaboration, product tutorials, customers. I need the site to address a comprehensive set of needs. I need that design to be consistent and thorough. I know what PlateHarbor is. I'm not using because I need more than a template that was customized. I need to be unique and match our brand thoughtfully, beautifully, and artistically. Someone asked me a question about how Murmly is similar to our tool in the way it is referred by end users and purchased by managers. Our website needs to primarily talk to the managers as I explained in the brief but it needs to appear cool and exciting to our end-users without focusing on the technology too much. Murmly is a tool that teams use to collaborate in small and large enterprises. The value prop for them is that communication is easier. But they don't put that on their website. Why? Because the users of the technology won't go to the website to find out information on it, they get their information from someone who is using it and demos it to them. When Ines tells her manager Otto "Lets get murmly, Ruth is using it at her company and its great" Ines's manager doesn't know anything about murmly so she promptly googles it. The most important thing from Ines's perspective is that Otto agrees to try it out. Otto's biggest concern is that productivity will be enhanced to degraded. Murmly knows this and so on the front page they know they are talking to Otto NOT Ines because Ines is already sold on it and doesn't need to get sold on the website. Ines is end user. Otto is the purchaser. We have the same problem and so our end users are not the ones purchasing our product, their managers are purchasing our product. We get referred by our end users and vetted by their managers. Hope this helps! Thank you for looking at this project!  Added Wednesday, June 7, 2017

Another observation I am having about the designs being submitted. I believe we used the animations on our current website because animations / cartoons connect with the "inner child" in our users. Whatever that means :-). I think it's what makes our brand fun. I have a hard time imagining that we could make the design fun looking without animations but I'm sure it can be achieved. I also recognize that blending pictures of real people and animations is hard. So either we must masterfully blend them, use only animations, or make the real people have a LOT of fun! So far most of the designs while achieve the goal of appealing to the serious Vice Presidents and directors, they are not doing a good job at appealing to the overworked program managers and bored employees. There seems to stand another challenge with animations which is animations are hard to find and/or create that achieve the message / emotion we are trying to communicate. I don't have any good answers for this but I will say we can hire both animators and illustrators if we need to. All you have to do is communicate the effect in the website design with some simpler version maybe not the end illustration or animation itself. Added Wednesday, June 7, 2017

• Sex appeal and a sense of humor. Copy that makes people excited and clairvoyant about our potential.
• Boring renditions of other non-inspiring websites

```html
<!DOCTYPE html>
<html lang="en">
<head>
<meta charset="utf-8">
<title>Plumvessel — How engagement happens</title>
<link href="https://fonts.googleapis.com/css2?family=Roboto:ital,wght@0,300;0,400;0,500;0,700;1,300;1,400&display=swap" rel="stylesheet">
<style>
:root{
  --blue:#17a5f2;
  --blue-dark:#0f8fd6;
  --sky:#5bbbe8;
  --green:#66c06b;
  --ink:#333a40;
  --muted:#8a9096;
  --line:#e3e7ea;
  --paper:#ffffff;
  --mist:#eef1f4;
  --teal:#2f5c68;
  --slate:#c8ccd0;
}
*{box-sizing:border-box;margin:0;padding:0}
html,body{width:1200px;height:3564px;overflow:hidden}
body{font-family:"Roboto",Arial,sans-serif;color:var(--ink);background:var(--paper);position:relative}
section,header,footer{position:relative;width:1200px;overflow:hidden}
.abs{position:absolute}
.brand{display:flex;align-items:center;gap:8px;font-size:22px;font-weight:400;color:var(--green)}
.brand-dot{width:22px;height:22px;border-radius:50%;border:3px solid var(--green)}
p{line-height:1.6}

/* hero */
.hero{height:504px}
.hero-photo{position:absolute;inset:0;background:linear-gradient(180deg,#ffffff 0%,#f3f6f8 18%,#c9d3db 45%,#7f8c99 75%,#5d6873 100%)}
.hero-photo::after{content:"";position:absolute;inset:0;background:linear-gradient(90deg,rgba(170,60,70,.18) 0%,rgba(0,0,0,0) 30%,rgba(40,60,110,.18) 65%,rgba(255,255,255,.25) 100%)}
.nav{position:absolute;top:28px;left:162px;right:162px;display:flex;align-items:center}
.nav-links{margin-left:auto;display:flex;gap:30px;align-items:center;font-size:11px;color:var(--ink)}
.nav-links .active{color:var(--blue);font-weight:500}
.btn-nav{border:1px solid var(--blue);padding:8px 12px;font-size:11px;color:var(--blue);background:#fff}
.hero-title{left:157px;top:112px;font-size:31px;font-weight:400;color:var(--blue);line-height:1.22;letter-spacing:.5px}
.hero-lede{left:511px;top:114px;width:540px;font-size:17px;line-height:1.45;color:var(--ink)}
.band{height:90px;background:var(--blue);color:#fff}
.band small{position:absolute;left:162px;top:20px;font-size:13px}
.band strong{position:absolute;left:162px;top:42px;font-size:21px;font-weight:400;letter-spacing:.5px}
.btn-ghost{position:absolute;border:1px solid #fff;color:#fff;font-size:11px;text-align:center}

/* features */
.features{height:542px}
.features h2{left:162px;top:93px;width:360px;font-size:22px;font-weight:400;line-height:1.2}
.features .intro{left:162px;top:166px;width:340px;font-size:11px;color:var(--muted)}
.scene{left:162px;top:249px;width:254px;height:226px;border-radius:8px;background:radial-gradient(ellipse at 50% 60%,#f3d9c3 0%,#f6e9dd 45%,#ffffff 75%)}
.card{position:absolute;width:226px;height:178px;padding:26px 24px}
.card.lead{background:var(--blue);color:#fff;box-shadow:0 8px 18px rgba(0,0,0,.18)}
.card h3{font-size:11px;font-weight:500;text-transform:uppercase;margin:14px 0 4px;line-height:1.35}
.card p{font-size:11px;line-height:1.5;color:var(--muted)}
.card.lead p{color:#fff}
.icon-ring{width:40px;height:40px;border-radius:50%;border:1.5px solid var(--blue);display:flex;align-items:center;justify-content:center}
.card.lead .icon-ring{border-color:#fff}

/* what we do */
.services{height:349px}
.services-photo{position:absolute;inset:0;background:linear-gradient(180deg,#4fb1e4 0%,#58b7e6 50%,#4aa9dc 100%)}
.services h2{width:100%;top:60px;text-align:center;color:#fff;font-size:31px;font-weight:300;letter-spacing:1px}
.service{position:absolute;top:130px;width:178px;height:178px;border-radius:50%;background:#fff;border:8px solid rgba(255,255,255,.55);background-clip:padding-box;display:flex;flex-direction:column;align-items:center;justify-content:center;gap:14px}
.service-badge{width:86px;height:86px;border-radius:50%;background:var(--blue);display:flex;align-items:center;justify-content:center}
.service span{font-size:18px;font-style:italic;font-weight:300;color:#333}

/* software */
.software{height:642px}
.app{left:159px;top:83px;width:428px;height:494px;background:#fff;box-shadow:0 6px 20px rgba(0,0,0,.15)}
.app-top{height:40px;display:flex;align-items:center;gap:10px;padding-left:8px;font-size:11px}
.app-side{position:absolute;left:0;top:40px;bottom:0;width:136px;background:var(--teal);padding-top:14px}
.app-side div{height:30px;font-size:8px;color:#d9e6ea;padding:10px 0 0 18px}
.app-side .on{background:#3f7584}
.app-main{position:absolute;left:136px;top:40px;right:0;bottom:0;background:#f3f5f6}
.filter{height:62px;background:#fff;box-shadow:0 3px 8px rgba(0,0,0,.15);padding:8px 12px;font-size:9px;color:var(--muted)}
.filter .row{display:flex;gap:6px;margin-top:10px;align-items:center}
.filter .sel{border:1px solid var(--line);padding:3px 8px;font-size:8px}
.meet{position:absolute;background:#fff;box-shadow:0 3px 8px rgba(0,0,0,.14);padding:8px 10px;font-size:8px;color:var(--muted)}
.person{display:flex;align-items:center;gap:8px;margin-top:14px;color:var(--ink)}
.avatar{width:26px;height:26px;border-radius:50%;background:var(--slate)}
.software-copy{left:661px;top:198px;width:390px}
.software-copy h2{font-size:25px;font-weight:400;line-height:1.25;margin-bottom:22px}
.software-copy p{font-size:11px;color:var(--muted);line-height:1.75}

/* how it works */
.works{height:605px}
.works h2{width:100%;top:88px;text-align:center;font-size:19px;font-weight:300;color:#666}
.sched{position:absolute;background:#fff;box-shadow:0 4px 14px rgba(0,0,0,.14);font-size:10px;color:var(--muted)}
.sched-head{height:22px;background:var(--sky);color:#fff;font-size:8px;padding:6px 10px}
.sched.front .sched-head{background:var(--blue)}
.slot{height:26px;border:1px solid var(--line);display:flex;align-items:center;justify-content:center;font-size:10px;color:var(--ink)}
.slot.pick{background:var(--blue);color:#fff;border-color:var(--blue)}
.slot.gone{background:var(--slate);color:#fff;border-color:var(--slate)}
.dots{top:510px;left:0;width:100%;display:flex;justify-content:center;gap:8px}
.dots i{width:10px;height:10px;border-radius:50%;background:#cfd4d8}
.dots i.on{background:var(--blue)}

/* cta */
.cta{height:333px}
.cta-photo{position:absolute;inset:0;background:linear-gradient(90deg,#5fb965 0%,#6cc570 45%,#5db763 100%)}
.cta h2{width:100%;top:86px;text-align:center;color:#fff;font-size:23px;font-weight:400;line-height:1.55;letter-spacing:.5px}
.btn-light{position:absolute;top:195px;width:190px;height:38px;background:#fff;color:var(--green);font-size:12px;text-align:center;line-height:38px;text-transform:uppercase}
.cta .btn-ghost{top:195px;height:38px;line-height:38px;font-size:12px;text-transform:uppercase}

/* info row */
.info{height:202px}
.info h4{font-size:13px;font-weight:500;color:var(--blue);margin-bottom:8px}
.news p{font-size:11px;color:var(--ink);line-height:1.5}
.more{font-size:11px;color:var(--blue);margin-top:8px;font-weight:500}
.quote{font-size:18px;font-style:italic;font-weight:300;line-height:1.35;color:var(--ink)}
.quote-by{font-size:9px;margin-top:8px;line-height:1.4;font-weight:500}
.quote-by span{color:var(--blue)}
.partners{display:grid;grid-template-columns:repeat(4,42px);gap:12px 14px;margin-top:10px}
.partners i{height:26px;border-radius:3px;background:var(--slate)}
.partners i:nth-child(odd){background:#b8c7d6}

/* footer */
.footer{height:297px;background:var(--mist)}
.footer .about{left:162px;top:120px;width:520px;font-size:11px;line-height:1.6}
.btn-solid{position:absolute;height:30px;line-height:30px;padding:0 14px;font-size:10px;background:var(--blue);color:#fff;text-transform:uppercase}
.btn-line{position:absolute;height:30px;line-height:30px;padding:0 14px;font-size:10px;border:1px solid var(--blue);color:var(--blue);background:#fff;text-transform:uppercase}
.foot-links{top:118px;left:765px;display:flex;gap:72px;font-size:10px;text-transform:uppercase}
.email{left:755px;top:190px;width:183px;height:30px;border-bottom:1px solid #cfd4d8;font-size:10px;color:var(--muted);padding-top:10px}
.legal{left:162px;right:162px;top:236px;border-top:1px solid #dfe3e6;padding-top:12px;display:flex;font-size:10px;color:var(--muted)}
.legal .links{margin-left:120px;display:flex;gap:24px;color:var(--ink)}
.legal .social{margin-left:auto;display:flex;gap:26px}
.legal .social i{width:12px;height:12px;border-radius:50%;background:#6b7278}
</style>
</head>
<body>

<header class="hero">
  <div class="hero-photo" role="img" aria-label="Photo of a team talking around a table with laptops and coffee"></div>
  <nav class="nav">
    <div class="brand"><span class="brand-dot"></span>Plumvessel</div>
    <div class="nav-links">
      <span class="active">Home</span><span>Product</span><span>About</span><span>Library</span><span>Careers</span><span>Contact</span>
      <span class="btn-nav">Register Now</span><span class="btn-nav">Login</span>
    </div>
  </nav>
  <h1 class="abs hero-title">HOW ENGAGEMENT<br>HAPPENS</h1>
  <p class="abs hero-lede">Plumvessel helps increase face-to-face engagement in your communities and groups with custom built solutions, training, consulting, and tools.</p>
</header>

<section class="band">
  <small>How we're going to change the world by</small>
  <strong>connecting people in-person</strong>
  <span class="btn-ghost" style="left:820px;top:31px;width:166px;height:28px;line-height:28px">Request Consultation</span>
</section>

<section class="features">
  <h2 class="abs">Increase face-to-face engagement in your communities and groups</h2>
  <p class="abs intro">Lorem ipsum dolor sit amet, consectetur adipiscing elit, sed do eiusmod tempor incididunt ut labore et dolore magna aliqua. Ut enim ad minim veniam, quis nostrud exercitation ullamco laboris nisi ut aliquip.</p>
  <div class="abs scene" role="img" aria-label="Illustration of two people chatting over coffee at a small table"></div>

  <div class="card lead" style="left:565px;top:76px">
    <div class="icon-ring"><svg width="20" height="20" viewBox="0 0 20 20" fill="#fff"><circle cx="10" cy="4" r="2"/><circle cx="4" cy="14" r="2"/><circle cx="16" cy="14" r="2"/></svg></div>
    <h3>Simplify face-to-face meetings</h3>
    <p>Lorem ipsum dolor sit amet, consectetur adipiscing.</p>
  </div>
  <div class="card" style="left:818px;top:76px">
    <div class="icon-ring"><svg width="20" height="20" viewBox="0 0 20 20" fill="#17a5f2"><circle cx="10" cy="4" r="2"/><circle cx="4" cy="14" r="2"/><circle cx="16" cy="14" r="2"/></svg></div>
    <h3>Maximize collaboration</h3>
    <p>Lorem ipsum dolor sit amet, consectetur adipiscing elit sed do.</p>
  </div>
  <div class="card" style="left:565px;top:296px">
    <div class="icon-ring"><svg width="20" height="20" viewBox="0 0 20 20" fill="none" stroke="#17a5f2" stroke-width="1.5"><path d="M4 10h12M12 6l4 4-4 4"/></svg></div>
    <h3>Enhance interactions</h3>
    <p>Lorem ipsum dolor sit amet, consectetur adipiscing elit sed do.</p>
  </div>
  <div class="card" style="left:818px;top:296px">
    <div class="icon-ring"><svg width="20" height="20" viewBox="0 0 20 20" fill="none" stroke="#17a5f2" stroke-width="1.5"><circle cx="10" cy="7" r="3"/><path d="M4 17c1-4 11-4 12 0"/></svg></div>
    <h3>Help people build relationships</h3>
    <p>Lorem ipsum dolor sit amet, consectetur adipiscing.</p>
  </div>
</section>

<section class="services">
  <div class="services-photo" role="img" aria-label="Blue-tinted photo of smiling people holding up paper speech bubbles"></div>
  <h2 class="abs">WHAT WE DO</h2>
  <div class="service" style="left:178px">
    <div class="service-badge"><svg width="40" height="44" viewBox="0 0 40 44" fill="none" stroke="#fff" stroke-width="3"><circle cx="20" cy="17" r="12"/><path d="M14 34h12M16 40h8"/></svg></div>
    <span>Solutions</span>
  </div>
  <div class="service" style="left:392px">
    <div class="service-badge"><svg width="40" height="40" viewBox="0 0 40 40" fill="#fff"><rect x="6" y="12" width="22" height="22"/><circle cx="17" cy="10" r="5"/><circle cx="30" cy="23" r="5"/></svg></div>
    <span>Consulting</span>
  </div>
  <div class="service" style="left:637px">
    <div class="service-badge"><svg width="44" height="40" viewBox="0 0 44 40" fill="none" stroke="#fff" stroke-width="2.5"><rect x="10" y="4" width="24" height="16"/><circle cx="10" cy="28" r="4"/><circle cx="34" cy="28" r="4"/><path d="M22 20v16"/></svg></div>
    <span>Training</span>
  </div>
  <div class="service" style="left:855px">
    <div class="service-badge"><svg width="40" height="40" viewBox="0 0 40 40" fill="none" stroke="#fff" stroke-width="4" stroke-linecap="round"><path d="M8 8l24 24M32 8L8 32"/></svg></div>
    <span>Tools</span>
  </div>
</section>

<section class="software">
  <div class="abs app">
    <div class="app-top"><span style="width:12px;height:10px;border-top:2px solid #999;border-bottom:2px solid #999"></span><span class="brand" style="font-size:11px;gap:4px"><span class="brand-dot" style="width:10px;height:10px;border-width:2px"></span>Plumvessel</span></div>
    <div class="app-side">
      <div>Availability</div><div class="on">Meetings</div><div>Groups</div><div>More</div>
    </div>
    <div class="app-main">
      <div class="filter">Meetings
        <div class="row">Filter by: <span class="sel">-Select-</span><span class="sel">Start date</span></div>
      </div>
      <div class="meet" style="left:14px;top:90px;width:170px;height:118px">Date: 2017-06-28
        <div class="person"><span class="avatar"></span>Hal Brenner</div>
        <div class="person"><span class="avatar"></span>Lou Fenwick</div>
      </div>
      <div class="meet" style="left:196px;top:90px;width:110px;height:118px">Date
        <div class="person"><span class="avatar"></span></div>
        <div class="person"><span class="avatar"></span></div>
      </div>
      <div class="meet" style="left:14px;top:226px;width:170px;height:118px">Date: 2017-06-22
        <div class="person"><span class="avatar"></span>Ivo Castell</div>
        <div class="person"><span class="avatar"></span>Pia Lundqvist</div>
      </div>
      <div class="meet" style="left:196px;top:226px;width:110px;height:118px">Date
        <div class="person"><span class="avatar"></span></div>
        <div class="person"><span class="avatar"></span></div>
      </div>
    </div>
  </div>
  <div class="abs software-copy">
    <h2>We're building software<br>that connects people in person</h2>
    <p>Lorem ipsum dolor sit amet, consectetur adipiscing elit, sed do eiusmod tempor incididunt ut labore et dolore magna aliqua. Ut enim ad minim veniam, quis nostrud exercitation ullamco laboris nisi ut aliquip ex ea commodo consequat. Duis aute irure dolor in reprehenderit in voluptate velit esse cillum dolore eu fugiat nulla pariatur. Excepteur sint occaecat cupidatat non proident, sunt in culpa qui officia deserunt mollit anim id est laborum. Sed ut perspiciatis unde omnis iste natus error sit voluptatem accusantium doloremque laudantium.</p>
  </div>
</section>

<section class="works">
  <h2 class="abs">Thats how Plumvessel works</h2>

  <div class="sched" style="left:337px;top:159px;width:170px;height:308px">
    <div class="sched-head">Schedule meeting with Nadia</div>
    <div style="padding:12px 10px;display:grid;gap:8px">
      <div style="text-align:center">Nadi</div><div>Mon, Jun 19, 2017</div>
      <div class="slot">12:00pm</div><div class="slot">12:30pm</div><div class="slot">1:00pm</div><div class="slot">1:30pm</div><div class="slot gone">2:00pm</div>
    </div>
  </div>
  <div class="sched" style="left:685px;top:159px;width:170px;height:308px">
    <div class="sched-head">&nbsp;</div>
    <div style="padding:12px 10px;display:grid;gap:8px">
      <div style="text-align:center">lity</div><div>&nbsp;</div>
      <div class="slot">12:15pm</div><div class="slot">12:45pm</div><div class="slot">1:15pm</div><div class="slot">1:45pm</div><div class="slot gone">2:15pm</div>
    </div>
  </div>

  <div class="sched front" style="left:461px;top:135px;width:273px;height:358px;z-index:2">
    <div class="sched-head">Schedule meeting with Nadia Pearson</div>
    <div style="padding:10px 12px">
      <div style="text-align:center;color:var(--ink);margin-bottom:10px">Nadia's availability</div>
      <div style="color:var(--ink);margin-bottom:8px">Mon, Jun 19, 2017</div>
      <div class="slot pick" style="margin-bottom:8px">12:00pm</div>
      <div style="display:grid;grid-template-columns:repeat(3,1fr);gap:4px;margin-bottom:10px">
        <div class="slot" style="height:22px;font-size:8px">30 mins</div><div class="slot pick" style="height:22px;font-size:8px">45 mins</div><div class="slot" style="height:22px;font-size:8px">1 hour</div>
      </div>
      <div style="display:grid;grid-template-columns:1fr 1fr;gap:7px">
        <div class="slot">12:15pm</div><div class="slot">12:30pm</div>
        <div class="slot">12:45pm</div><div class="slot">1:00pm</div>
        <div class="slot">1:15pm</div><div class="slot">1:30pm</div>
        <div class="slot gone">1:45pm</div><div class="slot gone">2:00pm</div>
      </div>
    </div>
  </div>

  <div class="abs dots"><i></i><i class="on"></i><i></i></div>
</section>

<section class="cta">
  <div class="cta-photo" role="img" aria-label="Green-tinted photo of a cheerful team laughing together"></div>
  <h2 class="abs">Because it takes the perfect team<br>to bring great innovations to life</h2>
  <span class="btn-light" style="left:406px">Request Demo</span>
  <span class="btn-ghost" style="left:608px;width:188px">Download Brochure</span>
</section>

<section class="info">
  <div class="abs news" style="left:159px;top:22px;width:300px">
    <h4>Latest News</h4>
    <p>07-06-2017</p>
    <p>Lorem ipsum dolor sit amet, consectetur adipiscing elit, sed do eiusmod tempor incididunt ut labore et dolore magna aliqua veniam.</p>
    <p class="more">Read More</p>
  </div>
  <div class="abs" style="left:511px;top:22px;width:290px">
    <h4>What Our Customer Say's:</h4>
    <p class="quote">“10 times better than the last mentor scheduling tool.”</p>
    <p class="quote-by">DALE FERRIN | UX Consultant<br>Founder <span>Northpine</span></p>
  </div>
  <div class="abs" style="left:834px;top:22px;width:210px">
    <h4>Our Experience With:</h4>
    <div class="partners"><i></i><i></i><i></i><i></i><i></i><i></i><i></i><i></i></div>
  </div>
</section>

<footer class="footer">
  <div class="abs brand" style="left:162px;top:60px;font-size:26px"><span class="brand-dot" style="width:26px;height:26px"></span>Plumvessel</div>
  <p class="abs about">Lorem ipsum dolor sit amet, consectetur adipiscing elit, sed do eiusmod tempor incididunt ut labore et dolore magna aliqua.</p>
  <span class="btn-solid" style="left:162px;top:182px">Request Demo</span>
  <span class="btn-line" style="left:278px;top:182px;border:none;background:transparent">Download Brochure</span>
  <div class="abs foot-links"><span>Contact</span><span>About</span><span>Impressum</span></div>
  <div class="abs email">Your email here</div>
  <span class="btn-line" style="left:962px;top:190px;height:26px;line-height:26px;padding:0 14px">Subscribe</span>
  <div class="abs legal">
    <span>© 2017 Plumvessel Inc. All rights reserved | Plumvessel® is a registered trademark of Plumvessel Inc.</span>
    <span class="links"><span>Blog</span><span>Press</span></span>
    <span class="social"><i></i><i></i><i></i></span>
  </div>
</footer>

</body>
</html>
```